Corvelle Meadow Organic Flower Farm, Farmer Florist

I am a flower grower and florist, so I do everything from the field to the vase. I want to include my website, phone, email and instagram

```html
<!DOCTYPE html>
<html lang="en">
<head>
<meta charset="utf-8">
<title>Corvelle Meadow – Business Card</title>
<link rel="stylesheet" href="https://fonts.googleapis.com/css2?family=Cinzel:wght@400;500&family=Arimo:wght@400&display=swap">
<style>
  :root {
    --backdrop: #e4e4e2;
    --paper: #f7f7f6;
    --wine: #5a2730;
    --wine-dark: #3d1a20;
    --wine-light: #7a3a44;
    --rose: #ee8b8e;
    --cream: #f6ece9;
    --ink: #3a2a2c;
  }
  * { margin: 0; padding: 0; box-sizing: border-box; }
  html, body { width: 1200px; height: 801px; overflow: hidden; }
  body {
    background: var(--backdrop);
    font-family: "Arimo", Arial, sans-serif;
    position: relative;
  }
  .card {
    position: absolute;
    top: 246px;
    width: 540px;
    height: 309px;
    overflow: hidden;
    box-shadow: 0 10px 24px rgba(0,0,0,0.18);
  }
  .card--front { left: 50px; background: var(--paper); }
  .card--back {
    left: 610px;
    background: radial-gradient(ellipse at 60% 35%, var(--wine-light) 0%, var(--wine) 45%, var(--wine-dark) 100%);
  }
  .card__wave { position: absolute; inset: 0; width: 100%; height: 100%; }

  .holder { position: absolute; top: 26px; right: 30px; text-align: right; }
  .holder__name { color: var(--rose); font-size: 18px; letter-spacing: 0.5px; text-transform: uppercase; }
  .holder__role { color: var(--ink); font-size: 13px; margin-top: 3px; }

  .brand {
    font-family: "Cinzel", Georgia, serif;
    font-weight: 500;
    letter-spacing: 3px;
    text-transform: uppercase;
    display: flex;
    align-items: center;
    gap: 10px;
  }
  .brand__mark { width: 11px; height: 11px; background: var(--rose); }
  .brand--front { position: absolute; left: 40px; top: 108px; font-size: 30px; color: var(--wine); }
  .brand--back {
    position: absolute; left: 0; right: 0; top: 130px;
    justify-content: center; font-size: 42px; color: var(--cream);
  }

  .address { position: absolute; left: 40px; top: 186px; color: var(--ink); font-size: 14px; line-height: 1.35; }

  .contacts { position: absolute; right: 22px; top: 168px; list-style: none; color: var(--cream); font-size: 13px; }
  .contacts__item { display: flex; justify-content: flex-end; align-items: center; gap: 9px; height: 23px; }
  .contacts__icon { width: 13px; height: 13px; flex: none; }
</style>
</head>
<body>

<section class="card card--front" aria-label="Card front">
  <svg class="card__wave" viewBox="0 0 540 309" preserveAspectRatio="none" aria-hidden="true">
    <path d="M540 95 C 420 100, 320 130, 270 195 C 220 260, 130 288, 0 290 L 0 309 L 540 309 Z" fill="var(--wine)"/>
    <path d="M540 82 C 415 88, 305 120, 255 188 C 205 255, 120 278, 0 280" fill="none" stroke="var(--rose)" stroke-width="5"/>
    <path d="M300 232 C 265 262, 215 280, 150 292" fill="none" stroke="var(--rose)" stroke-width="1.5"/>
  </svg>

  <div class="holder">
    <p class="holder__name">Marcus Hollin</p>
    <p class="holder__role">Manager</p>
  </div>

  <div class="brand brand--front">
    <span class="brand__mark"></span><span>Corvelle</span>
  </div>

  <p class="address">Your address, city<br>state, ZIP 0000</p>

  <ul class="contacts">
    <li class="contacts__item">555-018-2746
      <svg class="contacts__icon" viewBox="0 0 14 14" aria-hidden="true"><path d="M3 1 L5 1 L6 4 L4.5 5 C5.3 7 7 8.7 9 9.5 L10 8 L13 9 L13 11 C13 12 12 13 11 13 C6 13 1 8 1 3 C1 2 2 1 3 1 Z" fill="var(--rose)"/></svg>
    </li>
    <li class="contacts__item">info@corvellemeadow.com
      <svg class="contacts__icon" viewBox="0 0 14 14" aria-hidden="true"><rect x="1" y="3" width="12" height="8" fill="var(--rose)"/><path d="M1 3 L7 8 L13 3" fill="none" stroke="var(--wine)" stroke-width="1.2"/></svg>
    </li>
    <li class="contacts__item">www.corvellemeadow.com
      <svg class="contacts__icon" viewBox="0 0 14 14" aria-hidden="true"><circle cx="7" cy="7" r="6" fill="var(--rose)"/><path d="M1 7 H13 M7 1 C4 4 4 10 7 13 M7 1 C10 4 10 10 7 13" fill="none" stroke="var(--wine)" stroke-width="1"/></svg>
    </li>
    <li class="contacts__item">@corvellemeadow
      <svg class="contacts__icon" viewBox="0 0 14 14" aria-hidden="true"><rect x="1" y="1" width="12" height="12" rx="2" fill="var(--rose)"/></svg>
    </li>
  </ul>
</section>

<section class="card card--back" aria-label="Card back">
  <div class="brand brand--back">
    <span class="brand__mark"></span><span>Corvelle</span>
  </div>
</section>

</body>
</html>
```